Design of an image for use at trade shows ad expos

We provide Insurance Broking services to the Bus and Coach Industry and are looking for a design incorporating our logo (uploaded) that we can use as a basis for either banners or tiles that go onto trade booth walls or a stand alone booth. While open to designs, we would like to incorporate our primary colors which are:
Blue - Hex #001e62
Red - Hex #ba0c2f
Looking for a design / image that will print to approx. 1.5m x 1.5m

Industry/Entity Type

Insurance for Bus and Coaches

Other font styles liked:
• HELVETICA NEUE EXTENDED

```html
<!DOCTYPE html>
<html lang="en">
<head>
<meta charset="utf-8">
<title>FleetCover – Insurance Broking Services Banner</title>
<link rel="stylesheet" href="https://fonts.googleapis.com/css2?family=Archivo:wght@400;600;700&family=Russo+One&display=swap">
<style>
  :root {
    --navy: #27326a;
    --red: #a71d3f;
    --white: #ffffff;
    --mist: #ececee;
    --grey-text: #6b6b6f;
    --page: #ffffff;
  }
  * { margin: 0; padding: 0; box-sizing: border-box; }
  html, body {
    width: 747px;
    height: 1200px;
    overflow: hidden;
    background: var(--page);
  }
  .banner {
    position: absolute;
    left: 0;
    top: 226px;
    width: 747px;
    height: 747px;
    background: var(--white);
    overflow: hidden;
    box-shadow: 0 2px 6px rgba(0,0,0,0.25);
  }
  .banner__frame { position: absolute; inset: 0; width: 747px; height: 747px; }

  .skyline {
    position: absolute;
    left: 0; top: 90px;
    width: 747px; height: 55px;
    background: linear-gradient(180deg, rgba(236,236,238,0), var(--mist));
  }

  .brand {
    position: absolute;
    left: 168px;
    top: 56px;
    width: 440px;
  }
  .brand__name {
    font-family: "Russo One", sans-serif;
    font-size: 50px;
    line-height: 1;
    color: var(--navy);
    letter-spacing: 0.5px;
  }
  .brand__tagline {
    margin-top: 10px;
    font-family: "Archivo", sans-serif;
    font-weight: 600;
    font-size: 13px;
    color: var(--grey-text);
  }

  .headline {
    position: absolute;
    left: 0;
    width: 747px;
    text-align: center;
    font-family: "Russo One", sans-serif;
    color: var(--white);
    line-height: 1;
    white-space: nowrap;
  }
  .headline--main { top: 220px; font-size: 72px; letter-spacing: 1px; }
  .headline--sub { top: 288px; font-size: 55px; letter-spacing: 0.5px; }

  .sector {
    position: absolute;
    left: 94px;
    top: 363px;
    width: 560px;
    height: 53px;
    display: flex;
    border: 1.5px solid var(--white);
    font-family: "Archivo", sans-serif;
    font-weight: 600;
    font-size: 35px;
    line-height: 1;
    color: var(--white);
  }
  .sector__part {
    display: flex;
    align-items: center;
    white-space: nowrap;
  }
  .sector__part--red { background: var(--red); width: 199px; justify-content: center; }
  .sector__part--navy { background: var(--navy); flex: 1; padding-left: 6px; }

  .illustration--bus {
    position: absolute;
    left: 0; top: 442px;
    width: 541px; height: 240px;
    background: linear-gradient(180deg, #f4f4f4 0%, #dfe3e2 55%, #3a3a3a 100%);
    border-radius: 0 10px 10px 0;
  }
  .illustration--bus-stop {
    position: absolute;
    left: 584px; top: 453px;
    width: 97px; height: 247px;
    background: linear-gradient(180deg, #56628c 0%, #3f4a78 100%);
  }

  .web-address {
    position: absolute;
    left: 77px;
    top: 706px;
    font-family: "Archivo", sans-serif;
    font-weight: 600;
    font-size: 26px;
    line-height: 1;
    letter-spacing: 1.5px;
    color: var(--navy);
    white-space: nowrap;
  }
  .web-address__host { color: var(--red); }
</style>
</head>
<body>
<main class="banner">
  <svg class="banner__frame" viewBox="0 0 747 747" aria-hidden="true">
    <defs>
      <linearGradient id="heroGradient" x1="0" y1="0" x2="0" y2="1">
        <stop offset="0" stop-color="#26316a"/>
        <stop offset="0.45" stop-color="#2f3a70"/>
        <stop offset="0.6" stop-color="#242e63"/>
        <stop offset="1" stop-color="#283366"/>
      </linearGradient>
    </defs>
    <rect class="top-bar" x="0" y="0" width="747" height="18" fill="var(--navy)"/>
    <polygon class="skyline-band" points="0,118 747,118 747,145 690,145 655,169 0,169" fill="var(--mist)"/>
    <polygon class="hero-field" points="158,178 747,178 747,681 0,681 0,208 118,208" fill="url(#heroGradient)"/>
    <polygon class="road-band" points="0,670 747,670 747,747 517,747 454,695 0,695" fill="var(--red)"/>
  </svg>
  <div class="skyline" role="img" aria-label="Faint city skyline silhouette behind the brand name"></div>

  <div class="brand">
    <div class="brand__name">FleetCover</div>
    <div class="brand__tagline">Protecting the Bus and Coach Industry for 20 years</div>
  </div>

  <h1 class="headline headline--main">INSURANCE</h1>
  <h2 class="headline headline--sub">BROKING SERVICES</h2>

  <div class="sector">
    <span class="sector__part sector__part--red">BUS AND</span>
    <span class="sector__part sector__part--navy">COACH INDUSTRY</span>
  </div>

  <div class="illustration--bus" role="img" aria-label="Side view illustration of a white modern city bus"></div>
  <div class="illustration--bus-stop" role="img" aria-label="Illustration of a bus stop sign on a pole beside road markings"></div>

  <p class="web-address">www.<span class="web-address__host">fleetcover</span>.com.au</p>
</main>
</body>
</html>
```